Vantor Wear and Fuel is looking for a Clothing/Supplement Online Store Website!

Must be convenient, and user friendly, with vibrant colors that catch the eye!

Target Market(s)

Athletes, and Fashion Customers

Industry/Entity Type

Fitness

Coding

Coded - Design and coding required

Number of Pages Required

3 page

Font styles to use
Decorative

Colors

Designer to choose colors to be used in the design.

Requirements
Must have
• Somewhere to feature products, features to promote discounts and make announcements.
Nice to have
• My logos on each page

```html
<!DOCTYPE html>
<html lang="en">
<head>
<meta charset="utf-8">
<title>Vantor Wear and Fuel</title>
<link href="https://fonts.googleapis.com/css2?family=Open+Sans:wght@400;600;700&family=Raleway:wght@500;600;700&family=Rubik:wght@500;700&display=swap" rel="stylesheet">
<style>
:root{
  --red:#c4102c;
  --dark:#1f1f1f;
  --ink:#333;
  --muted:#777;
  --line:#d9d9d9;
  --blue:#3f86cf;
  --yellow:#f5e626;
  --light:#f2f2f2;
}
*{box-sizing:border-box;margin:0;padding:0}
html,body{width:1200px;height:4104px;overflow:hidden}
body{position:relative;background:#fff;font-family:'Open Sans',sans-serif;color:var(--ink)}
.abs{position:absolute}
.topbar{left:0;top:0;width:1200px;height:41px;background:var(--dark);color:#fff;font-size:12px}
.topbar .social{left:135px;top:0;height:41px;display:flex;gap:10px;align-items:center}
.topbar .social span{width:12px;height:12px;border-radius:50%;background:#fff;display:block}
.topbar .social .first{width:29px;height:41px;border-radius:0;background:var(--red);position:relative}
.topbar .social .first::after{content:"";position:absolute;left:9px;top:15px;width:11px;height:11px;border-radius:50%;background:#fff}
.topbar .links{right:143px;top:0;height:41px;display:flex;align-items:center;gap:14px}
.topbar .links i{font-style:normal;color:#888}
.header{left:0;top:41px;width:1200px;height:98px;border-bottom:1px solid #eee}
.brand{left:147px;top:22px;font-family:'Raleway',sans-serif;font-weight:700;font-size:46px;letter-spacing:1px;color:#444}
.search{left:805px;top:13px;width:252px;height:37px;border:1px solid #bbb;border-radius:19px;font-size:13px;display:flex;align-items:center;padding-left:34px;gap:14px;color:#333}
.search svg{flex:none}
.nav{left:531px;top:62px;width:526px;display:flex;justify-content:space-between;font-size:13px;font-weight:600;color:#444}
.nav .on{color:var(--red);border-bottom:2px solid var(--red);padding-bottom:4px}
.hero{left:0;top:139px;width:1200px;height:503px;background:linear-gradient(90deg,#c9c4c4,#d8d4d4 50%,#c6c2c3)}
.hero .photo{left:90px;top:0;width:450px;height:503px;background:linear-gradient(180deg,#b3a9a6,#8d8a92 60%,#6f7690)}
.hero .word{left:610px;top:108px;font-family:'Raleway',sans-serif;font-weight:700;font-size:96px;letter-spacing:2px;color:#3a3a3a}
.hero .tag{left:610px;top:258px;font-size:20px;font-weight:600;color:#333}
.hero .form{left:603px;top:317px;width:443px;height:54px;background:#fff;border:1px solid #ccc;border-radius:27px;display:flex;align-items:center;justify-content:space-between;padding:0 3px 0 27px;font-size:18px;color:#555}
.hero .form b{background:var(--red);color:#fff;height:46px;border-radius:23px;padding:0 22px;display:flex;align-items:center;font-size:17px}
.dots{left:571px;top:463px;display:flex;gap:6px}
.dots span{width:9px;height:9px;border-radius:50%;border:1px solid #fff}
.dots .on{background:#fff}
.tile{top:665px;width:277px;height:154px;border:2px solid #ddd}
.tile-label{top:837px;width:277px;text-align:center;font-size:12px;font-weight:700;color:#333}
.side-line{left:311px;top:869px;width:1px;height:857px;background:#e5e5e5}
.cat-title{left:29px;top:940px;font-family:'Raleway',sans-serif;font-weight:600;font-size:24px;color:#222}
.cat{left:29px;width:251px;height:54px;display:flex;justify-content:space-between;align-items:center;padding:0 16px 0 15px;font-size:15px;font-weight:700;color:#555}
.cat.on{background:#2b2b2b;color:#fff;font-size:13px;box-shadow:0 2px 4px rgba(0,0,0,.35)}
.sec-title{font-family:'Raleway',sans-serif;font-weight:600;font-size:29px;color:#222;text-align:center}
.pcard{width:212px;height:203px;border:2px solid #ddd;display:flex;align-items:center;justify-content:center}
.jar{width:96px;height:150px;border-radius:30px 30px 22px 22px}
.jar.black{background:linear-gradient(90deg,#111,#3a3a3a 40%,#111)}
.jar.silver{background:linear-gradient(90deg,#7a7a7a,#d0d0d0 40%,#6e6e6e)}
.jar.white{background:linear-gradient(90deg,#bdbdbd,#f1f1f1 40%,#b5b5b5)}
.pinfo{width:212px;text-align:center;font-size:14px;line-height:22px;color:#444}
.pinfo .price{color:var(--red);margin-top:12px}
.trend{left:0;top:1729px;width:1200px;height:417px;background:linear-gradient(90deg,#eeeeee,#e6e6e6)}
.trend .photo{left:526px;top:0;width:674px;height:417px;background:linear-gradient(90deg,#e9e9e9,#b9aca4 40%,#7a7a80)}
.trend .txt{left:115px;top:66px;width:430px;text-align:center}
.trend .t1{font-family:'Raleway',sans-serif;font-size:34px;color:#444}
.trend .t2{font-family:'Rubik',sans-serif;font-weight:700;font-size:40px;color:var(--red);margin-top:6px}
.trend .t3{font-size:16px;color:#333;margin-top:8px}
.trend .t4{font-family:'Rubik',sans-serif;font-weight:500;font-size:60px;color:var(--red);margin-top:8px;line-height:1.1}
.btn-line{left:210px;top:2056px;width:235px;height:1px;background:#999}
.btn-red{left:252px;top:2035px;width:153px;height:44px;background:var(--red);color:#fff;border-radius:22px;font-size:14px;font-weight:700;display:flex;align-items:center;justify-content:center}
.order{left:145px;top:2235px;width:910px;height:464px;background:#fff;box-shadow:0 0 14px rgba(0,0,0,.2)}
.ribbon{left:437px;top:2235px;width:328px;height:103px}
.ribbon span{position:absolute;left:0;top:20px;width:328px;text-align:center;color:#fff;font-family:'Raleway',sans-serif;font-size:38px;font-weight:500}
.order-img{left:193px;top:2367px;width:328px;height:300px;background:linear-gradient(180deg,#fff,#f1f1f1)}
.order-jar{left:272px;top:2387px;width:160px;height:240px;border-radius:44px 44px 30px 30px;background:linear-gradient(90deg,#111,#3d3d3d 40%,#0d0d0d)}
.otitle{left:550px;top:2374px;font-family:'Rubik',sans-serif;font-weight:700;font-size:33px;line-height:38px;color:var(--red)}
.oprice{left:550px;top:2460px;font-family:'Rubik',sans-serif;font-weight:500;font-size:31px;color:#222}
.qty{left:550px;top:2517px;display:flex;align-items:center;gap:12px;font-size:16px;color:#333}
.qty .box{width:93px;height:28px;border:1px solid #aaa;border-radius:14px;display:flex;justify-content:space-around;align-items:center;font-size:15px}
.qty .buy{width:115px;height:30px;background:var(--red);color:#fff;border-radius:15px;font-size:12px;font-weight:700;display:flex;align-items:center;justify-content:center}
.opara{left:550px;top:2556px;width:460px;font-size:12.5px;line-height:27px;color:#777}
.promo{top:2786px;height:325px}
.promo.blue{left:0;width:593px;background:linear-gradient(135deg,#5e9fde,#3a79c4)}
.promo.yellow{left:609px;width:591px;background:var(--yellow)}
.promo .img{background:linear-gradient(180deg,#1b1b1b,#3a3a3a 60%,#f4f4f4)}
.promo .h{font-family:'Raleway',sans-serif;font-size:26px;font-weight:500;text-align:center;width:300px}
.promo .big{font-family:'Rubik',sans-serif;font-weight:500;font-size:60px;text-align:center;width:340px}
.promo .btn{width:193px;height:40px;border:2px solid;font-size:13px;font-weight:700;display:flex;align-items:center;justify-content:center}
.ncard{top:3253px;width:295px}
.nimg{width:295px;height:198px;border:2px solid #ddd}
.nbox{margin:-4px 10px 0;background:#fff;box-shadow:0 2px 8px rgba(0,0,0,.15);height:113px;text-align:center;padding-top:12px}
.nbox b{display:block;font-weight:600;font-size:14px;color:#333}
.nbox p{font-size:11.5px;line-height:21px;color:#777;margin-top:4px}
.arrow{font-size:26px;color:#333;font-weight:400}
.brands{left:0;top:3606px;width:1200px;height:172px;background:var(--light)}
.bbox{top:36px;width:155px;height:86px;background:#fff;border:1px solid #e2e2e2;display:flex;align-items:center;justify-content:center}
.bbox span{display:block;width:90px;height:18px;background:#777;border-radius:2px}
.footer{left:0;top:3778px;width:1200px;height:326px;background:#1c1c1c;color:#fff}
.footer .ft{left:143px;top:66px;font-family:'Raleway',sans-serif;font-size:32px;font-weight:500}
.footer ul{list-style:none;font-size:14px;line-height:37px}
.footer li::before{content:"» ";}
.footer .soc{left:907px;top:139px;font-size:19px;font-weight:600}
.footer .circle{top:175px;width:36px;height:36px;border:2px solid #fff;border-radius:50%}
.footer .copy{left:0;top:276px;width:1200px;text-align:center;font-size:13px}
</style>
</head>
<body>

<div class="abs topbar">
  <div class="abs social"><span class="first"></span><span></span><span></span><span></span><span></span></div>
  <div class="abs links">Wishlist(0) <i>|</i> My Account <i>|</i> 0 Items <i>|</i> <b>$ 0.00</b></div>
</div>

<header class="abs header">
  <div class="abs brand">VANTOR</div>
  <div class="abs search">
    <svg width="14" height="14" viewBox="0 0 14 14"><circle cx="6" cy="6" r="4.5" fill="none" stroke="#222" stroke-width="2"/><line x1="9.5" y1="9.5" x2="13" y2="13" stroke="#222" stroke-width="2"/></svg>
    Search for products
  </div>
  <nav class="abs nav"><span class="on">HOME</span><span>PROTEIN PRODUCTS</span><span>VANTOR WEAR</span><span>HEALTH &amp; WELLNESS</span></nav>
</header>

<section class="abs hero">
  <div class="abs photo" role="img" aria-label="Smiling couple in casual clothes posing together"></div>
  <div class="abs word">VANTOR</div>
  <div class="abs tag">Register to get 50% OFF on FIRST Order...</div>
  <div class="abs form">Enter Your Email Address <b>REGISTER NOW</b></div>
  <div class="abs dots"><span class="on"></span><span></span><span></span><span></span></div>
</section>

<div class="abs tile" style="left:18px;background:linear-gradient(135deg,#cfd6dc,#3d6fc2 45%,#e8e2d4)" role="img" aria-label="Shaker bottle and protein powder on a kitchen table"></div>
<div class="abs tile" style="left:314px;background:linear-gradient(135deg,#6b7280,#d8c7b6 55%,#3a3a3a)" role="img" aria-label="Hand holding supplement capsules"></div>
<div class="abs tile" style="left:610px;background:linear-gradient(135deg,#5a3321,#c98d86 50%,#6a4026)" role="img" aria-label="Protein shake glass on a wooden table"></div>
<div class="abs tile" style="left:905px;background:linear-gradient(135deg,#9a8f84,#c7b8a8 50%,#7b6f67)" role="img" aria-label="Fit couple in athletic wear"></div>
<div class="abs tile-label" style="left:18px">OUR COMMITMENT TO QUALITY</div>
<div class="abs tile-label" style="left:314px">VANTOR FUEL</div>
<div class="abs tile-label" style="left:610px">PROTEIN RECEPES</div>
<div class="abs tile-label" style="left:905px">VANTOR WEAR</div>

<div class="abs side-line"></div>
<div class="abs cat-title">CATEGORY</div>
<div class="abs cat on" style="top:1009px">Protein <span>⌄</span></div>
<div class="abs cat" style="top:1090px">Nutrition <span>⌄</span></div>
<div class="abs cat" style="top:1163px">Amino Acids <span>⌄</span></div>
<div class="abs cat" style="top:1237px">Pre - Workout <span>⌄</span></div>
<div class="abs cat" style="top:1311px">Post - Workout <span>⌄</span></div>
<div class="abs cat" style="top:1384px">Creatine <span>⌄</span></div>
<div class="abs cat" style="top:1458px">Weight Gainer <span>⌄</span></div>
<div class="abs cat" style="top:1532px">Weight Management <span>⌄</span></div>
<div class="abs cat" style="top:1605px">Multi Vitamins <span>⌄</span></div>

<div class="abs sec-title" style="left:487px;top:936px;width:400px">SPECIAL PRODUCTS</div>

<div class="abs pcard" style="left:319px;top:1007px"><div class="jar black" role="img" aria-label="Black supplement jar"></div></div>
<div class="abs pcard" style="left:582px;top:1007px"><div class="jar silver" role="img" aria-label="Silver supplement jar"></div></div>
<div class="abs pcard" style="left:845px;top:1007px"><div class="jar white" role="img" aria-label="White supplement jar"></div></div>
<div class="abs pinfo" style="left:319px;top:1227px">Lorem Ipsum Sedat<br>Uta medues<div class="price">Price - $21.35</div></div>
<div class="abs pinfo" style="left:582px;top:1227px">Lorem Ipsum Sedat<br>Uta medues<div class="price">Price - $10.08</div></div>
<div class="abs pinfo" style="left:845px;top:1227px">Lorem Ipsum Sedat<br>Uta medues<div class="price">Price - $4.58</div></div>

<div class="abs pcard" style="left:319px;top:1348px"><div class="jar silver" role="img" aria-label="Silver supplement jar"></div></div>
<div class="abs pcard" style="left:582px;top:1348px"><div class="jar white" role="img" aria-label="White supplement jar"></div></div>
<div class="abs pcard" style="left:845px;top:1348px"><div class="jar black" role="img" aria-label="Black supplement jar"></div></div>
<div class="abs pinfo" style="left:319px;top:1567px">Lorem Ipsum Sedat<br>Uta medues<div class="price">Price - $4.63</div></div>
<div class="abs pinfo" style="left:582px;top:1567px">Lorem Ipsum Sedat<br>Uta medues<div class="price">Price - $4.58</div></div>
<div class="abs pinfo" style="left:845px;top:1567px">Lorem Ipsum Sedat<br>Uta medues<div class="price">Price - $3.59</div></div>

<section class="abs trend">
  <div class="abs photo" role="img" aria-label="Group of smiling women in sportswear holding yoga mats against a white brick wall"></div>
  <div class="abs txt">
    <div class="t1">Start Today !</div>
    <div class="t2">The Trends Benefits</div>
    <div class="t3">Select From Wide Range of Collection</div>
    <div class="t4">- 40% OFF</div>
  </div>
</section>
<div class="abs btn-line"></div>
<div class="abs btn-red">VIEW MORE</div>

<section class="abs order"></section>
<svg class="abs ribbon" viewBox="0 0 328 103" width="328" height="103" aria-hidden="true"><path d="M0 0H328V76L164 103L0 76Z" fill="#c4102c"/></svg>
<div class="abs ribbon" style="height:80px"><span>ORDER NOW</span></div>
<div class="abs order-img"></div>
<div class="abs order-jar" role="img" aria-label="Black supplement jar"></div>
<div class="abs otitle">Sed Utasumae Dolor<br>at 50% OFF</div>
<div class="abs oprice">$ 30.00</div>
<div class="abs qty">QUANTITY <span class="box"><span>−</span><span>1</span><span>+</span></span> <span class="buy">BUY NOW</span></div>
<p class="abs opara">Sed ut perspiciatis unde omnis iste natus sertror sit voluptatem accusant duium doloremque laudantium, totam rem aperiam, eaque ipsa quae ab Nemo enim ipsam voluptatem quia voluptar magni dolores.</p>

<section class="abs promo blue">
  <div class="abs img" style="left:30px;top:25px;width:160px;height:235px;border-radius:40px 40px 20px 20px" role="img" aria-label="Whey protein tub splashing in milk"></div>
  <div class="abs" style="left:0;top:250px;width:593px;height:75px;background:linear-gradient(180deg,rgba(255,255,255,.5),#f4f6fa)"></div>
  <div class="abs h" style="left:260px;top:73px;color:#fff">Just For You !</div>
  <div class="abs big" style="left:240px;top:116px;color:#fff">- 40% Off</div>
  <div class="abs btn" style="left:312px;top:203px;color:#fff;border-color:#fff">SO WHAT'S NEW</div>
</section>
<section class="abs promo yellow">
  <div class="abs" style="left:370px;top:10px;width:140px;height:305px;background:linear-gradient(180deg,#c28e6f,#2a2a2a 45%,#1d1d1d)" role="img" aria-label="Woman in black workout clothes with a resistance band"></div>
  <div class="abs h" style="left:24px;top:73px;color:#222">New Arrivals !</div>
  <div class="abs big" style="left:4px;top:116px;color:#222">- 20% Off</div>
  <div class="abs btn" style="left:80px;top:203px;color:var(--red);border-color:var(--red)">SO WHAT'S NEW</div>
</section>

<div class="abs sec-title" style="left:434px;top:3195px;width:400px">LATEST NEWS</div>
<div class="abs arrow" style="left:122px;top:3372px">‹</div>
<div class="abs arrow" style="left:1145px;top:3372px">›</div>
<article class="abs ncard" style="left:177px">
  <div class="nimg" style="background:linear-gradient(135deg,#6a4a34,#c79b74 50%,#3c2a1f)" role="img" aria-label="Scoop of protein powder"></div>
  <div class="nbox"><b>Lorem Ipsum is simple text</b><p>Lorem Ipsum has been the industry's std<br>dummy text ever since 1500.<br>→</p></div>
</article>
<article class="abs ncard" style="left:486px">
  <div class="nimg" style="background:linear-gradient(135deg,#8b8f96,#c9b5a3 50%,#4d4d52)" role="img" aria-label="Man mixing a protein shake"></div>
  <div class="nbox"><b>Lorem Ipsum is simple text</b><p>Lorem Ipsum has been the industry's std<br>dummy text ever since 1500.<br>→</p></div>
</article>
<article class="abs ncard" style="left:795px">
  <div class="nimg" style="background:linear-gradient(135deg,#b9bcc0,#3a3a3a 55%,#c6c7c9)" role="img" aria-label="Couple in black t-shirts"></div>
  <div class="nbox"><b>Lorem Ipsum is simple text</b><p>Lorem Ipsum has been the industry's std<br>dummy text ever since 1500.<br>→</p></div>
</article>

<section class="abs brands">
  <div class="abs arrow" style="left:93px;top:60px">‹</div>
  <div class="abs arrow" style="left:1122px;top:60px">›</div>
  <div class="abs bbox" style="left:183px"><span></span></div>
  <div class="abs bbox" style="left:373px"><span></span></div>
  <div class="abs bbox" style="left:563px"><span></span></div>
  <div class="abs bbox" style="left:752px"><span></span></div>
  <div class="abs bbox" style="left:942px"><span></span></div>
</section>

<footer class="abs footer">
  <div class="abs ft">VANTOR WEAR</div>
  <ul class="abs" style="left:143px;top:132px"><li>HOME</li><li>WHY US</li><li>NEWS &amp; EVENTS</li></ul>
  <ul class="abs" style="left:346px;top:132px"><li>SHIPPING DETAILS</li><li>OUR APPARELS</li><li>CONTACT US</li></ul>
  <div class="abs soc">Lets Get Social</div>
  <div class="abs circle" style="left:907px"></div>
  <div class="abs circle" style="left:959px"></div>
  <div class="abs circle" style="left:1012px"></div>
  <div class="abs copy">Copyrights © 2019 . All Rights Reserved.</div>
</footer>

</body>
</html>
```